​Silver Harbor Rhythm provides personal, friendly service in a fun and high energy environment. We are based in Vermont.

We would like a card that appeals to a wide range of audiences as we do a wide range of events. Please feel free to check out our website silverharborrhythm.net for inspiration.

Target Market(s)

weddings, corporate, birthday parties, colleges

Industry/Entity Type

Business

Contact Information for Business Card

Silver Harbor Rhythm
Providing Entertainment For All Occasions
555 274 9160
silverharborrhythm@mailnest.net
silverharborrhythm.net

```html
<!DOCTYPE html>
<html lang="en">
<head>
<meta charset="utf-8">
<title>Silver Harbor Rhythm – Business Card</title>
<link href="https://fonts.googleapis.com/css2?family=Open+Sans:wght@400;600;700&display=swap" rel="stylesheet">
<style>
  :root {
    --backdrop: #e8e5e0;
    --card: #ffffff;
    --brand-green: #3f6b2b;
    --ink: #1a1a1a;
    --text-grey: #555555;
    --icon-grey: #6b6b6b;
    --white: #ffffff;
  }
  * { box-sizing: border-box; margin: 0; padding: 0; }
  html, body {
    width: 1200px; height: 1200px; overflow: hidden;
    background: var(--backdrop);
    font-family: "Open Sans", Arial, sans-serif;
  }
  .canvas { position: relative; width: 1200px; height: 1200px; }
  .card {
    position: absolute; left: 160px; width: 880px; height: 540px;
    background: var(--card); border-radius: 26px; overflow: hidden;
    box-shadow: 0 6px 18px rgba(0,0,0,0.18);
  }
  .card-front { top: 35px; }
  .card-back { top: 625px; }

  .brand-name {
    position: absolute; left: 0; right: 0; text-align: center;
    color: var(--brand-green); font-weight: 700; letter-spacing: 1px;
  }
  .card-front .brand-name { top: 150px; font-size: 40px; }
  .card-back .brand-name { top: 200px; font-size: 54px; }

  .address {
    position: absolute; right: 500px; top: 285px; text-align: right;
    color: var(--text-grey); font-size: 20px; line-height: 36px;
  }
  .divider {
    position: absolute; left: 400px; top: 270px; width: 2px; height: 96px;
    background: #9a9a9a;
  }
  .contact-list {
    position: absolute; left: 418px; top: 266px; list-style: none;
    color: var(--text-grey); font-size: 20px;
  }
  .contact-item { display: flex; align-items: center; height: 35px; }
  .contact-icon { width: 20px; height: 20px; margin-right: 10px; flex: none; }

  .swoosh { position: absolute; left: 0; bottom: 0; width: 880px; height: 540px; }

  .person {
    position: absolute; right: 40px; top: 445px; text-align: right; color: var(--white);
  }
  .person-name { font-size: 26px; font-weight: 700; line-height: 32px; }
  .person-title { font-size: 18px; line-height: 26px; }

  .website {
    position: absolute; left: 0; right: 0; top: 330px; text-align: center;
    color: var(--text-grey); font-size: 28px; letter-spacing: 1.5px; font-weight: 600;
  }
</style>
</head>
<body>
<main class="canvas">

  <section class="card card-front" aria-label="Business card front">
    <svg class="swoosh" viewBox="0 0 880 540" aria-hidden="true">
      <path d="M0 455 C 250 418, 520 396, 880 392" fill="none" stroke="var(--brand-green)" stroke-width="3"/>
      <path d="M0 540 L0 488 C 240 446, 520 418, 880 410 L880 424 C 560 436, 300 476, 110 540 Z" fill="var(--brand-green)"/>
      <path d="M130 540 C 310 482, 570 446, 880 432 L880 540 Z" fill="var(--ink)"/>
    </svg>

    <h1 class="brand-name">Silver Harbor Rhythm</h1>

    <address class="address">
      Sreet Name, City Name<br>
      Zip Code-00000
    </address>
    <div class="divider"></div>
    <ul class="contact-list">
      <li class="contact-item">
        <svg class="contact-icon" viewBox="0 0 20 20" aria-hidden="true">
          <circle cx="10" cy="10" r="10" fill="var(--icon-grey)"/>
          <path d="M6.5 5 L8.5 5 L9.2 7.6 L8 8.6 C8.6 10 9.8 11.3 11.3 12 L12.3 10.8 L15 11.5 L15 13.5 C15 14.2 14.3 14.8 13.5 14.7 C9.2 14.2 5.8 10.8 5.3 6.5 C5.2 5.7 5.8 5 6.5 5 Z" fill="var(--white)"/>
        </svg>
        555 274 9160
      </li>
      <li class="contact-item">
        <svg class="contact-icon" viewBox="0 0 20 20" aria-hidden="true">
          <circle cx="10" cy="10" r="10" fill="var(--icon-grey)"/>
          <rect x="5" y="6.5" width="10" height="7" fill="var(--white)"/>
          <path d="M5 6.5 L10 10.5 L15 6.5" fill="none" stroke="var(--icon-grey)" stroke-width="1.2"/>
        </svg>
        silverharborrhythm@mailnest.net
      </li>
      <li class="contact-item">
        <svg class="contact-icon" viewBox="0 0 20 20" aria-hidden="true">
          <circle cx="10" cy="10" r="10" fill="var(--icon-grey)"/>
          <circle cx="10" cy="10" r="5" fill="none" stroke="var(--white)" stroke-width="1.3"/>
          <path d="M5 10 H15 M10 5 C8 7.5 8 12.5 10 15 M10 5 C12 7.5 12 12.5 10 15" fill="none" stroke="var(--white)" stroke-width="1.1"/>
        </svg>
        www.silverharborrhythm.net
      </li>
    </ul>

    <div class="person">
      <p class="person-name">Your Name</p>
      <p class="person-title">Title</p>
    </div>
  </section>

  <section class="card card-back" aria-label="Business card back">
    <h2 class="brand-name">Silver Harbor Rhythm</h2>
    <p class="website">www.silverharborrhythm.net</p>
  </section>

</main>
</body>
</html>
```